Velk Partners Building Business Cards

We need a business card that reflects our business as "Solar Experts" in San Diego. Browse our website www.velkpartners.example our License needs to be displayed as "CSLB# 3867140" our phone number is (619) 555-0187

Save thousands on your electric bills and increase the value of your home while helping to protect the environment. Our solar installation experts will help you design the system that's right for you, using only the highest quality equipment that will look great and give you ideal performance. Our goal is to make you energy independent, and get your electric bill to 0.

Paul Osterby
(619) 555-0187
paul@velkpartners.example

Target Market(s)

Home owners in san diego looking for solar

Industry/Entity Type

Solar Energy

Contact Information for Business Card

Paul Osterby
(619) 555-0187
paul@velkpartners.example

Font styles to use
Other font styles liked:
• Use our logo font

Requirements
Must have
• License needs to be displayed as "CSLB# 3867140" our phone number is (619) 555-0187
Nice to have
• Real images of rooftop home solar in san diego
Should not have
• our business address

```html
<!DOCTYPE html>
<html lang="en">
<head>
<meta charset="utf-8">
<title>Velk Partners Building – Business Cards</title>
<link rel="stylesheet" href="https://fonts.googleapis.com/css2?family=Source+Sans+3:wght@400;600;700&display=swap">
<style>
  :root {
    --navy: #1f3d7a;
    --gold: #f2b01e;
    --white: #ffffff;
    --card-light: #f6f3f2;
    --page: #e9e6e4;
    --sky-top: #2f7fd3;
    --sky-bottom: #9cc8ee;
    --panel-dark: #1a3f86;
  }
  * { margin: 0; padding: 0; box-sizing: border-box; }
  html, body { width: 1200px; height: 900px; overflow: hidden; }
  body {
    position: relative;
    background: var(--page);
    font-family: "Source Sans 3", "Myriad Pro", Arial, sans-serif;
  }
  .card {
    position: absolute;
    width: 556px;
    height: 343px;
    overflow: hidden;
    box-shadow: 0 6px 18px rgba(0,0,0,0.12);
  }
  .card-front { left: 238px; top: 62px; }
  .card-back { left: 459px; top: 518px; width: 560px; }

  .brand-area {
    height: 185px;
    background: var(--card-light);
    display: flex;
    align-items: center;
    justify-content: center;
  }
  .brand-name {
    color: var(--navy);
    font-weight: 700;
    font-size: 40px;
    letter-spacing: -0.5px;
    line-height: 1;
    padding-bottom: 8px;
  }
  .brand-name.faint { opacity: 0.28; font-size: 38px; }

  .contact-band {
    height: 158px;
    background: var(--navy);
    position: relative;
    color: var(--white);
    font-size: 15px;
  }
  .identity {
    position: absolute;
    right: 294px;
    top: 55px;
    text-align: right;
    line-height: 1.35;
  }
  .person-name { color: var(--gold); font-weight: 700; font-size: 18px; }
  .license-label { font-weight: 700; }
  .contact-list {
    position: absolute;
    left: 280px;
    top: 61px;
    list-style: none;
    line-height: 20px;
  }
  .contact-list li { display: flex; align-items: center; gap: 8px; }
  .contact-list svg { width: 12px; height: 12px; flex: none; }

  .back-brand { height: 187px; }
  .solar-photo {
    height: 156px;
    background: linear-gradient(160deg, var(--panel-dark) 0%, var(--panel-dark) 45%, var(--sky-top) 70%, var(--sky-bottom) 100%);
  }
</style>
</head>
<body>
  <section class="card card-front">
    <div class="brand-area">
      <div class="brand-name">Velk Partners Building</div>
    </div>
    <div class="contact-band">
      <div class="identity">
        <div class="person-name">Paul Osterby</div>
        <div><span class="license-label">License:</span> CSLB# 3867140</div>
      </div>
      <ul class="contact-list">
        <li>
          <svg viewBox="0 0 24 24" aria-hidden="true"><path fill="#f2b01e" d="M6.6 10.8a15.1 15.1 0 0 0 6.6 6.6l2.2-2.2c.3-.3.7-.4 1-.2 1.1.4 2.3.6 3.6.6.6 0 1 .4 1 1V20c0 .6-.4 1-1 1C10.6 21 3 13.4 3 4c0-.6.4-1 1-1h3.5c.6 0 1 .4 1 1 0 1.3.2 2.5.6 3.6.1.3 0 .7-.2 1z"/></svg>
          (619) 555-0187
        </li>
        <li>
          <svg viewBox="0 0 24 24" aria-hidden="true"><path fill="#f2b01e" d="M2 5h20v14H2z"/><path fill="none" stroke="#1f3d7a" stroke-width="2" d="M2 5l10 8 10-8"/></svg>
          paul@velkpartners.example
        </li>
      </ul>
    </div>
  </section>

  <section class="card card-back">
    <div class="brand-area back-brand">
      <div class="brand-name faint">Velk Partners Building</div>
    </div>
    <div class="solar-photo" role="img" aria-label="Photo of rooftop solar panels under a blue sky"></div>
  </section>
</body>
</html>
```